stationary deign for trucking company

im a trucking company looking for a professional set of stationary designs i deliver goods from point a to b
Updates

When submitting stationary designs I need envelope design, letterhead, cards, I’d badge etc

Industry/Entity Type

Trucking Company

Requirements
Must have
• must have letter head, business card, envelope, fax sheet, id badge, folder, thank you card, notebook, invoice sheet.
Nice to have
• nice to have them all custom made (letterhead,envelope, business card, I’d badge etc
Should not have
• must not have prepaid sign want i unique design for items

```html
<!DOCTYPE html>
<html lang="en">
<head>
<meta charset="utf-8">
<title>Harlow Freight Logistics – Presentation Folder</title>
<link href="https://fonts.googleapis.com/css2?family=Montserrat:wght@600&family=Arimo:wght@400&display=swap" rel="stylesheet">
<style>
  :root {
    --brand-blue: #1a5ba9;
    --ink: #1d2330;
    --paper: #ffffff;
    --pocket-grey: #d3d3d3;
    --cover-light: #f4f4f4;
    --cover-mid: #d9d9d9;
    --spine: #3a3f48;
    --page-bg: #ffffff;
  }
  html, body {
    margin: 0;
    width: 1200px;
    height: 1200px;
    overflow: hidden;
    background: var(--page-bg);
  }
  .folder-sheet { display: block; width: 1200px; height: 1200px; }
  .brand-name { font-family: "Montserrat", sans-serif; font-weight: 600; fill: var(--ink); }
  .contact-text { font-family: "Arimo", sans-serif; font-size: 8px; fill: var(--paper); }
  .contact-icon { fill: var(--paper); stroke: var(--brand-blue); }
</style>
</head>
<body>
<svg class="folder-sheet" viewBox="0 0 1200 1200" xmlns="http://www.w3.org/2000/svg">
  <defs>
    <linearGradient id="cover-fade" x1="0" y1="0" x2="1" y2="1">
      <stop offset="0" stop-color="var(--cover-mid)"/>
      <stop offset="0.55" stop-color="var(--cover-light)"/>
      <stop offset="1" stop-color="var(--cover-mid)"/>
    </linearGradient>
    <linearGradient id="photo-tone" x1="0" y1="0" x2="1" y2="1">
      <stop offset="0" stop-color="#c9d6ea"/>
      <stop offset="0.5" stop-color="#2f6cc0"/>
      <stop offset="1" stop-color="#14468a"/>
    </linearGradient>
  </defs>

  <!-- Outside spread: back cover and front cover -->
  <g class="outside-spread">
    <rect class="back-cover" x="178" y="24" width="422" height="550" fill="var(--paper)"/>
    <rect class="front-cover" x="600" y="24" width="422" height="550" fill="url(#cover-fade)"/>
    <line class="spine-fold" x1="600" y1="24" x2="600" y2="574" stroke="var(--spine)" stroke-width="1"/>

    <g class="contact-band">
      <rect x="238" y="470" width="361" height="86" fill="var(--brand-blue)"/>
      <rect class="contact-icon" x="228" y="486" width="8" height="8" rx="1"/>
      <rect class="contact-icon" x="228" y="510" width="8" height="8" rx="1"/>
      <rect class="contact-icon" x="228" y="520" width="8" height="8" rx="1"/>
      <rect class="contact-icon" x="228" y="530" width="8" height="8" rx="1"/>
      <text class="contact-text" x="248" y="493">YOUR ADDRESS HERE</text>
      <text class="contact-text" x="248" y="502">12345</text>
      <text class="contact-text" x="248" y="517">00022 333</text>
      <text class="contact-text" x="248" y="527">info@harlowfreight.com</text>
      <text class="contact-text" x="248" y="537">harlowfreight.com</text>
    </g>

    <g class="brand-mark">
      <rect x="724" y="72" width="22" height="22" fill="var(--brand-blue)"/>
      <text class="brand-name" x="756" y="88" font-size="21" letter-spacing="2">HARLOW</text>
      <text class="brand-name" x="757" y="98" font-size="6" letter-spacing="1.2">FREIGHT · LOGISTICS</text>
    </g>

    <polygon class="cover-photo" role="img" aria-label="Blue-toned photo of a lorry on a motorway under clouds"
      points="600,156 1014,416 600,574" fill="url(#photo-tone)"/>
  </g>

  <!-- Inside spread: two pockets -->
  <g class="inside-spread">
    <rect class="inside-panel" x="178" y="622" width="844" height="552" fill="var(--brand-blue)"/>
    <line class="inside-fold" x1="600" y1="658" x2="600" y2="1174" stroke="#e6eaf2" stroke-width="1.5"/>
    <path class="pocket-left" d="M178 982 H380 C500 982 590 1060 600 1174 H178 Z" fill="var(--pocket-grey)"/>
    <path class="pocket-right" d="M1022 982 H820 C700 982 610 1060 600 1174 H1022 Z" fill="var(--pocket-grey)"/>
  </g>
</svg>
</body>
</html>
```